Business Card Design

New business card design

Target Market(s)

Residential & Commercial Property Managers

Industry/Entity Type

Plumbing Services

Contact Information for Business Card

Name - Rowan Keddle, title - Director, Phone Number - 0431 286 517, email - rowan@tbk-plumbing.com.au, Company ABN - 73 215 904 386,

Font styles to use
Sans Serif

Colors
0054AA
0677BA
7BADD7
CADEEF
E8F1F8

```html
<!DOCTYPE html>
<html lang="en">
<head>
<meta charset="utf-8">
<title>TBK Plumbing Services – Business Card</title>
<link rel="stylesheet" href="https://fonts.googleapis.com/css2?family=PT+Sans:ital,wght@0,400;0,700;1,400&family=PT+Sans+Narrow&display=swap">
<style>
  :root {
    --page: #ffffff;
    --card: #060809;
    --frame: #6b625a;
    --taupe: #8a8077;
    --tagline: #766c64;
    --white: #ffffff;
    --aqua: #37c5f1;
    --steel: #8ab3c8;
    --drop: #2ea7e0;
    --ink: #0b0d10;
  }
  * { margin: 0; padding: 0; box-sizing: border-box; }
  html, body {
    width: 1000px; height: 1200px; overflow: hidden;
    background: var(--page);
    font-family: "PT Sans", sans-serif;
  }
  .sheet { position: relative; width: 1000px; height: 1200px; }
  .card {
    position: absolute; left: 176px; width: 648px; height: 370px;
    background: var(--card); overflow: hidden;
  }
  .card--front { top: 170px; }
  .card--back { top: 642px; }
  .card-art { position: absolute; inset: 0; width: 648px; height: 370px; }

  .wordmark {
    position: absolute; left: 0; right: 0; display: flex;
    justify-content: center; align-items: flex-end; gap: 10px;
    color: var(--white); font-weight: 400; line-height: 1;
  }
  .wordmark-dot { border-radius: 50%; background: var(--drop); }
  .card--front .wordmark { top: 62px; font-size: 128px; letter-spacing: 6px; }
  .card--front .wordmark-dot { width: 26px; height: 26px; margin-bottom: 22px; }
  .card--back .wordmark { top: 22px; font-size: 88px; letter-spacing: 4px; }
  .card--back .wordmark-dot { width: 18px; height: 18px; margin-bottom: 15px; }

  .tagline {
    position: absolute; left: 0; right: 0; text-align: center;
    font-family: "PT Sans Narrow", sans-serif; color: var(--tagline);
    text-transform: lowercase; line-height: 1;
  }
  .card--front .tagline { top: 246px; font-size: 20px; letter-spacing: 17px; padding-left: 17px; }
  .card--back .tagline { top: 141px; font-size: 15px; letter-spacing: 12px; padding-left: 12px; }

  .abn {
    position: absolute; left: 0; right: 0; top: 337px; text-align: center;
    font-size: 17px; color: var(--ink); letter-spacing: 0.2px;
  }

  .divider-dots {
    position: absolute; top: 181px; left: 0; right: 0;
    display: flex; justify-content: center; gap: 12px;
  }
  .divider-dots span { width: 5px; height: 5px; border-radius: 50%; background: var(--taupe); }

  .contact { position: absolute; left: 0; right: 0; text-align: center; color: var(--taupe); line-height: 1; }
  .contact-name { top: 209px; font-size: 29px; font-weight: 400; }
  .contact-title { top: 247px; font-size: 20px; font-style: italic; }
  .contact-line { display: flex; justify-content: center; align-items: center; gap: 8px; font-size: 18px; }
  .contact-phone { top: 281px; }
  .contact-email { top: 309px; }
  .contact-icon { width: 16px; height: 16px; fill: var(--taupe); }
</style>
</head>
<body>
<div class="sheet">

  <section class="card card--front" aria-label="Business card front">
    <svg class="card-art" viewBox="0 0 648 370" aria-hidden="true">
      <defs>
        <linearGradient id="tab-fill" x1="0" y1="0" x2="0" y2="1">
          <stop offset="0" stop-color="var(--steel)"/>
          <stop offset="1" stop-color="var(--aqua)"/>
        </linearGradient>
      </defs>
      <path d="M0 356 H166 Q190 356 204 337 L212 327 Q222 323 232 323 H414 Q424 323 434 327 L442 337 Q456 356 480 356 H648 V370 H0 Z" fill="url(#tab-fill)"/>
      <path d="M23 23 H625 V332 H484 Q478 332 472 324 L462 311 Q448 301 426 301 H222 Q200 301 186 311 L176 324 Q170 332 164 332 H23 Z" fill="none" stroke="var(--frame)" stroke-width="1.2"/>
    </svg>
    <div class="wordmark"><span class="wordmark-text">tbk</span><span class="wordmark-dot"></span></div>
    <p class="tagline">plumbing services</p>
    <p class="abn">ABN - 73 215 904 386</p>
  </section>

  <section class="card card--back" aria-label="Business card back">
    <svg class="card-art" viewBox="0 0 648 370">
      <defs>
        <linearGradient id="band-fill" x1="0" y1="0" x2="1" y2="0">
          <stop offset="0" stop-color="var(--steel)"/>
          <stop offset="1" stop-color="var(--aqua)"/>
        </linearGradient>
      </defs>
      <rect x="0" y="0" width="130" height="370" fill="url(#band-fill)" role="img" aria-label="Decorative blue water artwork"/>
      <rect x="23" y="23" width="602" height="324" fill="none" stroke="var(--frame)" stroke-width="1.2"/>
    </svg>
    <div class="wordmark"><span class="wordmark-text">tbk</span><span class="wordmark-dot"></span></div>
    <p class="tagline">plumbing services</p>
    <div class="divider-dots"><span></span><span></span><span></span></div>
    <h1 class="contact contact-name">Rowan Keddle</h1>
    <p class="contact contact-title">Director</p>
    <p class="contact contact-line contact-phone">
      <svg class="contact-icon" viewBox="0 0 24 24" aria-hidden="true"><path d="M6.6 10.8a15.1 15.1 0 0 0 6.6 6.6l2.2-2.2a1 1 0 0 1 1-.25 11.4 11.4 0 0 0 3.6.57 1 1 0 0 1 1 1V20a1 1 0 0 1-1 1A17 17 0 0 1 3 4a1 1 0 0 1 1-1h3.5a1 1 0 0 1 1 1c0 1.25.2 2.46.57 3.6a1 1 0 0 1-.25 1z"/></svg>
      <span>0431 286 517</span>
    </p>
    <p class="contact contact-line contact-email">
      <svg class="contact-icon" viewBox="0 0 24 24" aria-hidden="true"><path d="M2 6h20v2l-10 6L2 8z M2 10l10 6 10-6v9H2z"/></svg>
      <span>rowan@tbk-plumbing.com.au</span>
    </p>
  </section>

</div>
</body>
</html>
```